Substance abuse awareness flyer for school age kids

I am needing a flyer for school-age kids. What if it were designed to look like an Quorby with someone texting and the text bubbles were some of the text below with emojis? Maybe a text chain between to friends:

Maybe the first text bubble says "I'm thinking about using drugs and alcohol"
the next bubble: "Just say no!" ( perhaps a stop sign emoji ?)

"Talk to your parents, your teachers at school, or your doctor about how drugs and alcohol can harm you"

another text bubble "did you know that alcohol and drugs could lead to..."
then include some of the info below (see links for more info).
Where ever you get info, it must be cited.

this needs to be English on one side and Spanish on the other side and needs to include the logo attached.

The effects of substance abuse
RMQ: https://www.rmqhealthnet.org/plwtrk/vesk/features/teen-substance-use.html
Affect growth and development, especially brain development. Not able to focus at school or be around friends. https://www.halvenstudy.org/sites/default/files/youthguide_2.pdf
Leads to risky behaviors and lack of impulse control (dangerous activities) https://www.halvenstudy.org/sites/default/files/youthguide_2.pdf
Contribute to health problems as an adult: heart disease, high blood pressure, and trouble sleeping.

Target Market(s)

school age kids 9-20

Requirements
Must have
• Print ready: 8.5x11

```html
<!DOCTYPE html>
<html lang="en">
<head>
<meta charset="utf-8">
<title>Say No to Drugs and Alcohol – Flyer</title>
<link href="https://fonts.googleapis.com/css2?family=Montserrat:wght@500;600;700&display=swap" rel="stylesheet">
<style>
  :root{
    --page-bg:#eeeeee;
    --field-green:#48b34c;
    --band-green:#6fbf5a;
    --button-green:#48b34c;
    --lime:#bfd630;
    --sky:#74cde0;
    --maroon:#5e2637;
    --alert-red:#ec2227;
    --ink:#111111;
    --white:#ffffff;
    --bullet-blue:#1f74c4;
  }
  *{box-sizing:border-box;margin:0;padding:0}
  html,body{width:1029px;height:1200px;overflow:hidden;background:var(--page-bg)}
  body{font-family:"Montserrat",Arial,sans-serif;color:var(--ink)}
  .flyer{position:absolute;left:62px;top:0;width:904px;height:1200px;background:var(--white);overflow:hidden}
  .backdrop{position:absolute;left:0;top:0}
  .figure{position:absolute}
  .figure--left{left:0;top:155px;width:241px;height:463px;background:linear-gradient(160deg,#5a3fa6,#8a4fa8 55%,#c9b9e2)}
  .figure--right{left:665px;top:323px;width:239px;height:509px;background:linear-gradient(200deg,#5a3fa6,#6a4f9e 55%,#c9b9e2)}
  .bubble-text{position:absolute;font-weight:700}
  .bubble-text--ask{left:161px;top:56px;width:300px;font-size:19.5px;line-height:22px;font-weight:600;letter-spacing:.3px}
  .bubble-text--no{left:472px;top:164px;font-size:24px}
  .bubble-text--talk{left:326px;top:233px;width:330px;font-size:18px;line-height:21.5px}
  .bubble-text--facts{left:273px;top:400px;width:390px;font-size:20.5px;line-height:23.6px}
  .source{display:block;text-align:right;color:var(--white);font-size:18px;margin-top:2px}
  .brand{position:absolute;left:718px;top:44px;width:150px;height:80px;display:flex;align-items:center;gap:8px}
  .brand-dot{width:16px;height:16px;border-radius:50%;background:var(--maroon);flex:none}
  .brand-name{font-size:15px;line-height:18px;font-weight:700;color:var(--maroon)}
  .risks-tab{position:absolute;left:0;top:700px;width:368px;height:42px;background:var(--alert-red);border-radius:0 22px 22px 0;color:var(--white);font-weight:700;font-size:24px;line-height:42px;padding-left:11px}
  .risks-list{position:absolute;left:10px;top:765px;list-style:none;font-size:19px;line-height:23.5px;font-weight:500}
  .risks-list li{position:relative;padding-left:13px;margin-bottom:21px}
  .risks-list li::before{content:"";position:absolute;left:0;top:10px;width:6px;height:6px;border-radius:50%;background:var(--bullet-blue)}
  .summary{position:absolute;left:0;top:939px;width:904px;height:162px;background:var(--band-green);padding:11px 12px;font-weight:700;font-size:23.5px;line-height:29px}
  .cta{position:absolute;left:214px;top:1129px;width:489px;height:60px;border-radius:30px;background:var(--button-green);color:var(--white);font-weight:700;font-size:28.5px;line-height:60px;text-align:center}
</style>
</head>
<body>
<main class="flyer">
  <svg class="backdrop" width="904" height="1200" viewBox="0 0 904 1200" aria-hidden="true">
    <path d="M0,0 H904 V850 C800,846 680,830 560,780 C420,715 250,612 0,607 Z" fill="var(--field-green)"/>
    <path d="M904,850 C800,846 680,830 560,780 C420,715 250,612 0,607" fill="none" stroke="var(--maroon)" stroke-width="7"/>
    <!-- ask bubble -->
    <path d="M125,24 L572,18 Q589,18 589,34 L589,197 Q589,213 572,213 L136,200 Q115,198 115,182 L115,40 Q115,25 125,24 Z" transform="translate(0,0)" fill="none"/>
    <path d="M131,24 L573,18 Q589,18 589,34 V197 Q589,213 573,212 L252,198 L211,219 L211,198 L131,196 Q115,196 115,180 V40 Q115,24 131,24 Z" transform="translate(0,-2) scale(1,0.69) translate(0,10)" fill="var(--lime)"/>
    <!-- just say no -->
    <path d="M470,140 L650,146 Q660,146 660,156 V192 Q660,202 650,202 L624,205 L625,216 L598,205 L470,211 Q459,211 459,201 V150 Q459,140 470,140 Z" fill="var(--sky)"/>
    <!-- talk bubble -->
    <path d="M325,221 L652,231 Q665,232 665,245 V330 Q665,343 652,343 L582,345 L582,356 L553,344 L325,356 Q310,356 310,342 V235 Q310,221 325,221 Z" fill="var(--sky)"/>
    <!-- facts bubble -->
    <path d="M278,382 L650,394 Q665,395 665,410 V578 Q665,593 650,593 L578,596 L578,614 L547,596 L278,599 Q261,599 261,583 V398 Q261,382 278,382 Z" fill="var(--sky)"/>
  </svg>

  <div class="figure figure--left" role="img" aria-label="Illustration of a young man seen from behind, holding a phone with a lime screen"></div>
  <div class="figure figure--right" role="img" aria-label="Illustration of a young man seen from behind, holding a phone with a blue screen"></div>

  <p class="bubble-text bubble-text--ask">I'M THINKING ABOUT USING DRUGS AND ALCOHOL</p>
  <p class="bubble-text bubble-text--no">JUST SAY NO!</p>
  <p class="bubble-text bubble-text--talk">Talk to your parents, your teachers at school, or your doctor about how drugs and alcohol can harm you.</p>
  <p class="bubble-text bubble-text--facts">Did you know that alcohol and drugs could lead to - The development of chronic diseases and other serious problems including: High blood pressure, heart disease, stroke, liver disease, and digestive problems.<span class="source">-rmq.gov</span></p>

  <div class="brand"><span class="brand-dot"></span><span class="brand-name">Northbend Care Group</span></div>

  <h2 class="risks-tab">RISKS OF SUBSTANCE USE</h2>
  <ul class="risks-list">
    <li>Affect the growth and development of teens,<br>especially brain development.</li>
    <li>Occur more frequently with other risky behaviors.</li>
    <li>If you use drugs and alcohol at an early age,<br>it increases your chances of becoming addicted later in life</li>
  </ul>

  <p class="summary">Finally, the earlier teens start using substances, the greater their chances of continuing to use substances and developing substance use problems later in life. When teens begin drinking at an early age, they increase the chance of becoming addicted to or continuing to abuse substances later in life.</p>

  <p class="cta">Say No to Drugs and Alcohol!</p>
</main>
</body>
</html>
```